we can communicate on this, but i want to follow the approach we took on Pellew|Marsh & Quinlan but i feel the card front needs the black background and the platinum and gold logo. The back? I am open. we can use the same info from PM&Q. Velmont Arc is an enhanced equity investment fund - basically a very exclusive boutique hedge fund that uses only stock options. very advanced things. hope you are interested

Contact Information for Business Card

Dr. Lewis T. Brennick, CFA
Scientifique de fusée financière
701.555.0143
LTBquant47@mailvantor.com

4718 Willow Creek Bend W.
West Fargo, ND 58078

No web site

Colors

Designer to choose colors to be used in the design.

Requirements
Nice to have
• I tend to prefer the most visible applications of the logo to include logo and name, the logo version with a black background and the gold and platinum components separated by the black. I see this working well for a single side (logo and name - this is card front to me).
• I am fairly open to other treatments on the reverse side with the data. To me, it makes sense to have a different color rendition of the logo on the reverse and it may be a muted black tone on tone or an oversized portion that would have spot UV. Or, the reverse may play with colors and layout
Should not have
• Other colors = no no
• Decorative font

```html
<!DOCTYPE html>
<html lang="en">
<head>
<meta charset="utf-8">
<title>Velmont Arc — Business Card</title>
<link href="https://fonts.googleapis.com/css2?family=Montserrat:wght@400;600;700&family=Open+Sans:wght@400;600&display=swap" rel="stylesheet">
<style>
  :root {
    --backdrop: #2b2d31;
    --card-black: #141416;
    --card-white: #ffffff;
    --gold: #d1ae4a;
    --ink: #1c1c1e;
    --ink-soft: #3a3a3c;
    --platinum: #e6e4ea;
  }
  * { box-sizing: border-box; margin: 0; padding: 0; }
  html, body {
    width: 1200px; height: 900px; overflow: hidden;
    background: var(--backdrop);
  }
  .canvas {
    width: 1200px; height: 900px;
    display: flex; flex-direction: column; align-items: center; justify-content: center;
    gap: 48px;
  }
  .card {
    position: relative;
    width: 660px; height: 377px;
    border-radius: 34px;
    overflow: hidden;
    box-shadow: 0 14px 30px rgba(0,0,0,0.45);
  }

  /* Front */
  .card-front { background: var(--card-black); }
  .front-lockup {
    position: absolute; inset: 0;
    display: flex; align-items: center; justify-content: center; gap: 18px;
  }
  .front-lockup .mark-dot {
    width: 64px; height: 64px; border-radius: 50%;
    background: var(--gold);
  }
  .front-lockup .brand-name {
    font-family: 'Montserrat', sans-serif; font-weight: 700;
    font-size: 46px; letter-spacing: 1px; text-transform: uppercase;
    color: var(--platinum);
  }

  /* Back */
  .card-back { background: var(--card-white); }
  .back-swoosh { position: absolute; inset: 0; width: 100%; height: 100%; }
  .back-lockup {
    position: absolute; left: 40px; top: 130px; width: 260px;
    display: flex; flex-direction: column; align-items: center; gap: 14px;
  }
  .back-lockup .mark-dot {
    width: 60px; height: 60px; border-radius: 50%;
    background: var(--gold);
  }
  .back-lockup .brand-name {
    font-family: 'Montserrat', sans-serif; font-weight: 700;
    font-size: 30px; letter-spacing: 1px; text-transform: uppercase;
    color: var(--ink);
  }
  .divider {
    position: absolute; left: 318px; top: 70px;
    width: 1px; height: 200px; background: var(--gold);
  }
  .contact {
    position: absolute; left: 342px; top: 64px;
    font-family: 'Open Sans', sans-serif; color: var(--ink-soft);
  }
  .contact .person-name {
    font-family: 'Montserrat', sans-serif; font-weight: 700;
    font-size: 26px; color: var(--gold); text-transform: uppercase; letter-spacing: 0.5px;
  }
  .contact .person-title {
    font-family: 'Montserrat', sans-serif; font-weight: 600;
    font-size: 17px; color: var(--ink); margin-top: 2px;
  }
  .contact .address { font-size: 14px; line-height: 1.35; margin-top: 10px; }
  .contact .lines { list-style: none; margin-top: 10px; font-size: 14.5px; }
  .contact .lines li { display: flex; align-items: center; gap: 10px; line-height: 1.75; }
  .contact .lines svg { width: 14px; height: 14px; flex: none; }
  .contact .accent { color: var(--gold); }
</style>
</head>
<body>
<main class="canvas">

  <section class="card card-front" aria-label="Card front">
    <div class="front-lockup">
      <span class="mark-dot" aria-hidden="true"></span>
      <span class="brand-name">Velmont Arc</span>
    </div>
  </section>

  <section class="card card-back" aria-label="Card back">
    <svg class="back-swoosh" viewBox="0 0 660 377" preserveAspectRatio="none" aria-hidden="true">
      <path d="M0 377 L0 340 C210 322 450 268 660 200 L660 377 Z" fill="var(--gold)"/>
      <path d="M260 318 C420 288 550 244 660 192 L660 200 C550 252 420 294 260 318 Z" fill="var(--ink)"/>
      <path d="M290 308 C440 278 560 234 660 181 L660 185 C560 239 440 284 290 308 Z" fill="var(--gold)"/>
    </svg>

    <div class="back-lockup">
      <span class="mark-dot" aria-hidden="true"></span>
      <span class="brand-name">Velmont Arc</span>
    </div>

    <div class="divider" aria-hidden="true"></div>

    <div class="contact">
      <p class="person-name">Tomas Reinholt</p>
      <p class="person-title">Doctor</p>
      <p class="address">Harbor Lane loc, Dunmere<br>Ashby stand, 30817</p>
      <ul class="lines">
        <li>
          <svg viewBox="0 0 24 24" aria-hidden="true"><path fill="var(--gold)" d="M6.6 10.8a15 15 0 0 0 6.6 6.6l2.2-2.2a1 1 0 0 1 1-.25 11.4 11.4 0 0 0 3.6.6 1 1 0 0 1 1 1V20a1 1 0 0 1-1 1A17 17 0 0 1 3 4a1 1 0 0 1 1-1h3.5a1 1 0 0 1 1 1c0 1.25.2 2.45.6 3.6a1 1 0 0 1-.25 1z"/></svg>
          310-555-0182
        </li>
        <li>
          <svg viewBox="0 0 24 24" aria-hidden="true"><rect x="2" y="5" width="20" height="14" rx="2" fill="var(--gold)"/><path d="M3 6l9 7 9-7" fill="none" stroke="#fff" stroke-width="2"/></svg>
          info@arcfieldnet.com.au
        </li>
        <li>
          <svg viewBox="0 0 24 24" aria-hidden="true"><circle cx="12" cy="12" r="10" fill="var(--gold)"/><path d="M2 12h20M12 2c3 3 3 17 0 20M12 2c-3 3-3 17 0 20" fill="none" stroke="#fff" stroke-width="1.5"/></svg>
          <span>www.<span class="accent">arcfieldnet.com</span>.au</span>
        </li>
      </ul>
    </div>
  </section>

</main>
</body>
</html>
```